Danielle Voskuijl Photography
Letterhead & Business Card Design
Danielle Voskuijl Photography - Photography
Creative Brief
Professional
Danielle Voskuijl
Photographer / Owner
418 Bramblecrest Lane Fort McMurray, AB T9K 2P7
daniellevoskuijlphotography@quillmarrow.example
www.daniellevoskuijlphotography.example
I think I'd like to include a photo I've taken...thoughts?

```html
<!DOCTYPE html>
<html lang="en">
<head>
<meta charset="utf-8">
<title>Danielle Voskuijl Photography – Business Cards</title>
<link href="https://fonts.googleapis.com/css2?family=Open+Sans:ital,wght@0,400;0,600;1,700&display=swap" rel="stylesheet">
<style>
  :root {
    --backdrop: #3b3b3d;
    --card: #ffffff;
    --brand-blue: #1f9fd1;
    --brand-brown: #9a6746;
    --ink: #4a4a4a;
    --rule: #b9b9b9;
    --ring: #5fb8cf;
  }
  html, body {
    margin: 0;
    padding: 0;
    width: 1200px;
    height: 852px;
    overflow: hidden;
    background: var(--backdrop);
    font-family: "Open Sans", Arial, sans-serif;
  }
  .canvas {
    position: relative;
    width: 1200px;
    height: 852px;
  }
  .card {
    position: absolute;
    width: 560px;
    height: 310px;
    background: var(--card);
    border-radius: 16px;
    overflow: hidden;
    box-shadow: 0 8px 24px rgba(0,0,0,.35);
    color: var(--ink);
  }
  .card--horizontal { left: 70px; top: 90px; }
  .card--stacked { left: 570px; top: 450px; }

  .card__accent {
    position: absolute;
    left: 0; right: 0; bottom: 0;
    height: 24px;
    background: var(--brand-blue);
    border-top: 4px solid #fff;
    box-shadow: 0 -3px 0 var(--brand-brown);
  }

  .brand {
    position: absolute;
    display: flex;
    align-items: center;
    gap: 18px;
  }
  .brand__mark {
    width: 84px;
    height: 84px;
    border-radius: 50%;
    border: 6px solid var(--ring);
    box-sizing: border-box;
    flex: none;
  }
  .brand__name {
    color: var(--brand-brown);
    font-weight: 400;
    font-size: 26px;
    line-height: 1.15;
    letter-spacing: .5px;
  }
  .card--horizontal .brand { left: 90px; top: 34px; }

  .card--stacked .brand {
    left: 28px; top: 56px;
    width: 180px;
    flex-direction: column;
    gap: 12px;
    text-align: center;
  }
  .card--stacked .brand__name { font-size: 17px; }

  .identity {
    position: absolute;
    font-size: 12.5px;
    line-height: 1.45;
  }
  .identity__name {
    margin: 0;
    color: var(--brand-blue);
    font-weight: 700;
    font-style: italic;
    font-size: 17px;
  }
  .identity__title {
    margin: 0 0 12px;
    color: var(--brand-brown);
    font-size: 13px;
  }
  .identity__address { margin: 0; }
  .card--horizontal .identity { left: 38px; top: 158px; width: 170px; }
  .card--stacked .identity { left: 238px; top: 34px; }

  .divider {
    position: absolute;
    width: 1px;
    background: var(--rule);
  }
  .card--horizontal .divider { left: 214px; top: 162px; height: 100px; }
  .card--stacked .divider { left: 222px; top: 40px; height: 210px; }

  .contacts {
    position: absolute;
    list-style: none;
    margin: 0;
    padding: 0;
    font-size: 11.5px;
    line-height: 1;
  }
  .contacts li {
    display: flex;
    align-items: center;
    gap: 7px;
    margin-bottom: 9px;
    white-space: nowrap;
  }
  .contacts .contacts__email { font-size: 10.5px; }
  .contacts svg { width: 13px; height: 13px; flex: none; }
  .card--horizontal .contacts { left: 228px; top: 166px; }
  .card--stacked .contacts { left: 238px; top: 160px; }
</style>
</head>
<body>
<svg width="0" height="0" style="position:absolute" aria-hidden="true">
  <defs>
    <symbol id="icon-phone" viewBox="0 0 16 16">
      <path d="M4 1.5 6.3 4 5 5.6c.8 2 2.4 3.6 4.4 4.4L11 8.7 13.5 11l-1.6 2.8C7 13.5 2.5 9 2.2 4z" fill="#1f9fd1"/>
    </symbol>
    <symbol id="icon-mobile" viewBox="0 0 16 16">
      <rect x="4" y="1" width="8" height="14" rx="1.6" fill="#1f9fd1"/>
      <rect x="5.4" y="3" width="5.2" height="8.5" fill="#fff"/>
      <circle cx="8" cy="13.2" r=".8" fill="#fff"/>
    </symbol>
    <symbol id="icon-mail" viewBox="0 0 16 16">
      <circle cx="8" cy="8" r="8" fill="#1f9fd1"/>
      <rect x="4" y="5" width="8" height="6" rx=".6" fill="#fff"/>
      <path d="M4.3 5.4 8 8.3l3.7-2.9" fill="none" stroke="#1f9fd1" stroke-width=".9"/>
    </symbol>
    <symbol id="icon-web" viewBox="0 0 16 16">
      <circle cx="8" cy="8" r="7" fill="none" stroke="#1f9fd1" stroke-width="1.6"/>
      <ellipse cx="8" cy="8" rx="3" ry="7" fill="none" stroke="#1f9fd1" stroke-width="1.2"/>
      <path d="M1.5 8h13" stroke="#1f9fd1" stroke-width="1.2"/>
    </symbol>
  </defs>
</svg>

<main class="canvas">
  <article class="card card--horizontal">
    <div class="brand">
      <span class="brand__mark"></span>
      <span class="brand__name">Danielle Voskuijl<br>Photography</span>
    </div>
    <div class="identity">
      <p class="identity__name">Danielle Voskuijl</p>
      <p class="identity__title">Photographer / Owner</p>
      <p class="identity__address">418 Bramblecrest Lane<br>Fort McMurray, AB T9K 2P7</p>
    </div>
    <span class="divider"></span>
    <ul class="contacts">
      <li><svg><use href="#icon-phone"/></svg>780.555.0143</li>
      <li><svg><use href="#icon-mobile"/></svg>780.555.0178</li>
      <li class="contacts__email"><svg><use href="#icon-mail"/></svg>daniellevoskuijlphotography@quillmarrow.example</li>
      <li><svg><use href="#icon-web"/></svg>www.daniellevoskuijlphotography.example</li>
    </ul>
    <div class="card__accent"></div>
  </article>

  <article class="card card--stacked">
    <div class="brand">
      <span class="brand__mark"></span>
      <span class="brand__name">Danielle Voskuijl<br>Photography</span>
    </div>
    <span class="divider"></span>
    <div class="identity">
      <p class="identity__name">Danielle Voskuijl</p>
      <p class="identity__title">Photographer / Owner</p>
      <p class="identity__address">418 Bramblecrest Lane<br>Fort McMurray, AB T9K 2P7</p>
    </div>
    <ul class="contacts">
      <li><svg><use href="#icon-phone"/></svg>780.555.0143</li>
      <li><svg><use href="#icon-mobile"/></svg>780.555.0178</li>
      <li class="contacts__email"><svg><use href="#icon-mail"/></svg>daniellevoskuijlphotography@quillmarrow.example</li>
      <li><svg><use href="#icon-web"/></svg>www.daniellevoskuijlphotography.example</li>
    </ul>
    <div class="card__accent"></div>
  </article>
</main>
</body>
</html>
```